K7 Electrical Services Ltd Web design

I require a web site for my new electrical contracting company. We are customer service orientated. Offering high value electrical installations, design and maintenance. Focused on custom residential and commercial upgrading. Lighting design and application are paramount in our company's services. Industry leading product use and integration are always on the forefront with our customer client services. As well as energy efficiency.

Target Market(s)

Homebuilders, General Contractors, Property management companies, clients, individuals,

Industry/Entity Type

Electric Company

Coding

Coded - Design and coding required

Number of Pages Required

3 page

Requirements
Must have
• Classic, modern, edgy but not trendy . Appeals to the masse.
• 3 page
• home page
• about page
• gallery page
• ability to contact from the webiste
Nice to have
• open to all types of designs that are relative to the construction industry.
• Black, Grey, metallic ice blue and deep purple colours from the logo.
Should not have
• anything cheesy with cartoon light bulb images.

```html
<!DOCTYPE html>
<html lang="en">
<head>
<meta charset="utf-8">
<title>K7 Electrical Services Ltd</title>
<link href="https://fonts.googleapis.com/css2?family=Exo+2:wght@400;500;600;700;800&family=Open+Sans:wght@400;600&display=swap" rel="stylesheet">
<style>
:root{
  --purple:#6b2f94;
  --purple-bright:#8a3fc2;
  --dark:#2f2f2f;
  --charcoal:#262626;
  --black:#141414;
  --grey-light:#f1f1f1;
  --grey-text:#6d6d6d;
  --ink:#1b1b1b;
  --white:#ffffff;
  --heading:"Exo 2",sans-serif;
  --body:"Open Sans",sans-serif;
}
*{box-sizing:border-box;margin:0;padding:0}
html,body{width:1200px;height:4423px;overflow:hidden}
body{font-family:var(--body);color:var(--ink);background:var(--white);position:relative}
section,header,footer{position:absolute;left:0;width:1200px}
.abs{position:absolute}
.brand{font-family:var(--heading);font-weight:700;letter-spacing:1px;line-height:1.1;text-transform:uppercase}

/* header */
.site-header{top:0;height:105px;background:var(--white)}
.site-header .brand{left:60px;top:28px;font-size:22px;color:var(--purple);width:240px}
.main-nav{right:60px;top:46px;display:flex;gap:34px;font-family:var(--heading);font-weight:600;font-size:15px;text-transform:uppercase;color:var(--ink)}

/* hero */
.hero{top:105px;height:580px;background:var(--dark);overflow:hidden}
.hero svg.hero-shape{position:absolute;left:0;top:0}
.hero h1{left:60px;top:70px;width:480px;font-family:var(--heading);font-weight:800;font-size:44px;line-height:1.1;color:var(--white);text-transform:uppercase}
.hero .lead{left:60px;top:232px;width:420px;font-size:16px;line-height:1.45;color:#bdbdbd}
.perks{left:60px;top:305px;list-style:none}
.perks li{display:flex;align-items:center;gap:14px;color:var(--white);font-size:15px;height:34px}
.perks .dot{width:20px;height:20px;border-radius:50%;background:var(--purple-bright);display:flex;align-items:center;justify-content:center}
.btn{display:flex;align-items:center;justify-content:center;gap:12px;font-family:var(--body);font-size:17px;color:var(--white);background:var(--purple-bright)}
.hero .btn{left:60px;top:468px;width:175px;height:48px}
.hero .brand{left:620px;top:215px;width:500px;text-align:center;font-size:60px;color:var(--white)}

/* booking */
.booking{top:684px;left:60px;width:1080px;height:254px;background:var(--white);box-shadow:0 4px 18px rgba(0,0,0,.15)}
.booking h2{left:25px;top:28px;font-family:var(--heading);font-weight:500;font-size:38px;color:var(--ink)}
.emergency{left:750px;top:27px;width:345px;height:50px;background:var(--dark);color:var(--white);display:flex;align-items:center;gap:12px;padding-left:24px;font-size:16px}
.field label{display:block;font-size:14px;margin-bottom:6px}
.field .box{height:56px;border:1px solid #cfcfcf;background:var(--white);font-size:13px;color:#999;display:flex;align-items:center;justify-content:space-between;padding:0 14px}
.booking .btn{left:874px;top:140px;width:182px;height:56px}

/* who */
.who h2,.section-title{font-family:var(--heading);font-weight:800;font-size:44px;text-align:center;width:1200px;text-transform:uppercase;color:var(--ink)}
.who{top:938px;height:492px}
.who h2{top:80px;left:0}
.who p{left:160px;top:150px;width:880px;text-align:center;font-size:15.5px;line-height:1.55;color:#333}
.video{top:1223px;left:60px;width:1080px;height:510px;z-index:2;border:4px solid var(--white);box-shadow:0 6px 20px rgba(0,0,0,.3);background:linear-gradient(135deg,#5e5a55 0%,#8f8a84 45%,#cfcac3 100%)}
.video .play{position:absolute;left:496px;top:211px}

/* services */
.services{top:1430px;height:988px;background:var(--purple)}
.service{width:360px;text-align:center;color:var(--white)}
.service .icon{display:block;margin:0 auto;width:80px;height:66px}
.service h3{font-family:var(--heading);font-weight:500;font-size:24px;margin:22px 0 18px}
.service p{font-size:14.5px;line-height:1.5;width:300px;margin:0 auto;color:#eadff2}

/* projects */
.projects{top:2418px;height:294px}
.projects h2{top:80px;left:0}
.projects p{left:320px;top:144px;width:560px;text-align:center;font-size:15.5px;line-height:1.5}
.cta-band{left:0;top:230px;width:1200px;height:64px;display:flex}
.cta-band a{flex:1;display:flex;align-items:center;justify-content:center;gap:14px;color:var(--white);text-decoration:none;font-size:18px}
.cta-band .call{background:var(--dark)}
.cta-band .appoint{background:var(--purple)}

/* testimonials */
.reviews{top:2712px;height:878px}
.reviews .section-title{top:88px;left:0}
.reviews .base{left:0;top:422px;width:1200px;height:456px;background:var(--dark)}
.quote-card{left:60px;top:183px;width:648px;height:348px;background:var(--grey-light)}
.quote-card .mark{left:40px;top:20px;font-family:var(--heading);font-weight:800;font-size:260px;line-height:.8;color:#e4e4e4}
.quote-card h3{left:225px;top:70px;font-family:var(--heading);font-weight:500;font-size:26px}
.quote-card p{left:94px;top:128px;width:460px;text-align:center;font-size:16px;line-height:1.6;color:#333}
.quote-photo{left:708px;top:183px;width:432px;height:348px;background:linear-gradient(160deg,#3a3a3a 0%,#7b7b80 45%,#c7c5c2 100%)}
.reviews svg.tail{position:absolute;left:400px;top:531px}
.reviews .brand{left:0;top:640px;width:1200px;text-align:center;font-size:30px;color:var(--white)}
.reviews .tagline{left:180px;top:722px;width:840px;text-align:center;color:var(--white);font-size:15.5px;line-height:1.6}
.reviews .tagline strong{font-family:var(--heading);font-weight:500;font-size:22px}
.social{left:534px;top:800px;display:flex;gap:12px}
.social span{width:42px;height:42px;border-radius:50%;background:var(--white);display:block}

/* newsletter */
.newsletter{top:3590px;height:375px}
.newsletter h2{left:60px;top:140px;font-family:var(--heading);font-weight:500;font-size:40px}
.newsletter .sub{left:60px;top:192px;font-size:15px;color:var(--grey-text)}
.newsletter .input{left:60px;top:236px;width:392px;height:44px;border:1px solid #cfcfcf;font-size:13px;color:#aaa;padding:0 14px;display:flex;align-items:center}
.newsletter .btn{left:452px;top:236px;width:156px;height:44px;font-size:15px}
.newsletter .person{left:855px;top:20px;width:300px;height:355px;background:linear-gradient(180deg,#d9d9d9 0%,#3850a8 55%,#26377c 100%);border-radius:140px 140px 0 0}

/* footer */
.site-footer{top:3965px;height:458px;background:var(--charcoal);overflow:hidden}
.site-footer svg.foot-shape{position:absolute;left:0;top:0}
.site-footer .brand{left:40px;top:200px;width:420px;font-size:46px;color:var(--white);text-align:center}
.site-footer h2{left:604px;top:40px;font-family:var(--heading);font-weight:500;font-size:29px;color:var(--white)}
.office{color:var(--white);width:260px}
.office h3{font-family:var(--heading);font-weight:600;font-size:18px;margin-bottom:18px}
.office .row{display:flex;gap:14px;font-size:13.5px;line-height:1.4;margin-bottom:18px;color:#ddd}
.pin{flex:none;width:22px;height:22px;border-radius:50%;background:var(--purple-bright);display:flex;align-items:center;justify-content:center}
.copyright{left:0;top:422px;width:1200px;height:36px;background:var(--black);color:#ddd;font-size:13px;display:flex;align-items:center;justify-content:center}
</style>
</head>
<body>

<header class="site-header">
  <div class="abs brand">K7 Electrical<br>Services Ltd</div>
  <nav class="abs main-nav"><span>Home</span><span>About</span><span>Services</span><span>Pages</span><span>Our Prices</span><span>FAQ</span><span>Blog</span><span>Contact Us</span></nav>
</header>

<section class="hero">
  <svg class="hero-shape" width="1200" height="580" viewBox="0 0 1200 580"><polygon points="600,0 1200,0 1200,580 448,580" fill="#6b2f94"/></svg>
  <h1 class="abs">Cover yourself with residential safety</h1>
  <p class="abs lead">Premier electrical contractor, Voltcrest Electrical Services responds with licensed electricians.</p>
  <ul class="abs perks">
    <li><span class="dot"><svg width="10" height="10" viewBox="0 0 10 10"><path d="M3 1l4 4-4 4" stroke="#fff" stroke-width="2" fill="none"/></svg></span>Upfront Pricing Guarantee</li>
    <li><span class="dot"><svg width="10" height="10" viewBox="0 0 10 10"><path d="M3 1l4 4-4 4" stroke="#fff" stroke-width="2" fill="none"/></svg></span>Best Value Guarantee</li>
    <li><span class="dot"><svg width="10" height="10" viewBox="0 0 10 10"><path d="M3 1l4 4-4 4" stroke="#fff" stroke-width="2" fill="none"/></svg></span>No Phone Guessing Guarantee</li>
    <li><span class="dot"><svg width="10" height="10" viewBox="0 0 10 10"><path d="M3 1l4 4-4 4" stroke="#fff" stroke-width="2" fill="none"/></svg></span>No Scare Tactics Guarantee</li>
  </ul>
  <a class="abs btn">About us <svg width="34" height="10" viewBox="0 0 34 10"><path d="M0 5h32M27 1l5 4-5 4" stroke="#fff" stroke-width="2" fill="none"/></svg></a>
  <div class="abs brand">K7 Electrical<br>Services Ltd</div>
</section>

<section class="booking">
  <h2 class="abs">Book Us Today &amp; Let’s Get Started!</h2>
  <div class="abs emergency"><svg width="20" height="20" viewBox="0 0 20 20"><circle cx="10" cy="10" r="9" stroke="#fff" stroke-width="1.5" fill="none"/><path d="M6 7c1 4 3 6 7 7l1-2-2-1-1 1c-1-1-2-2-2-3l1-1-1-2z" fill="#fff"/></svg>We take emergency calls as well</div>
  <div class="abs field" style="left:25px;top:114px;width:198px"><label>Name</label><div class="box"></div></div>
  <div class="abs field" style="left:240px;top:114px;width:200px"><label>Email</label><div class="box"></div></div>
  <div class="abs field" style="left:458px;top:114px;width:190px"><label>Phone</label><div class="box"></div></div>
  <div class="abs field" style="left:668px;top:114px;width:186px"><label>Type of service</label><div class="box">Residential<svg width="14" height="8" viewBox="0 0 14 8"><path d="M0 0h14L7 8z" fill="#222"/></svg></div></div>
  <a class="abs btn">Book us <svg width="34" height="10" viewBox="0 0 34 10"><path d="M0 5h32M27 1l5 4-5 4" stroke="#fff" stroke-width="2" fill="none"/></svg></a>
</section>

<section class="who">
  <h2 class="abs">Who we are</h2>
  <p class="abs">Our years of experience, along with our diverse and specialty services, have made it possible to successfully complete commercial projects for retail centers, grocery stores, professional offices, banks, auto dealerships and tenant complexes.</p>
</section>

<section class="services">
  <div class="abs service" style="left:40px;top:395px"><svg class="icon" viewBox="0 0 80 66"><path d="M6 30h68v10c0 10-8 16-18 16H24C14 56 6 50 6 40z M16 56l-4 8M64 56l4 8M14 30V8c0-4 6-6 9-2" stroke="#fff" stroke-width="3" fill="none"/></svg><h3>Bath Remodeling</h3><p>On a par with kitchen remodels, bath remodels weigh in as an investment that will pay off when it comes time to sell.</p></div>
  <div class="abs service" style="left:420px;top:395px"><svg class="icon" viewBox="0 0 80 66"><rect x="12" y="2" width="56" height="56" stroke="#fff" stroke-width="3" fill="none"/><circle cx="40" cy="30" r="20" stroke="#fff" stroke-width="3" fill="none"/><circle cx="40" cy="30" r="4" fill="#fff"/></svg><h3>Ceiling Fan Install</h3><p>Ceiling fans are great for circulating both warm air &amp; cool air for year-round comfort, but they can be tricky.</p></div>
  <div class="abs service" style="left:800px;top:395px"><svg class="icon" viewBox="0 0 80 66"><path d="M20 60V36l20-12V4M40 24l20 12v24M40 24v20" stroke="#fff" stroke-width="3" fill="none"/><circle cx="40" cy="4" r="3" fill="#fff"/><circle cx="20" cy="62" r="3" fill="#fff"/><circle cx="60" cy="62" r="3" fill="#fff"/><circle cx="40" cy="46" r="3" fill="#fff"/></svg><h3>Circuit Additions</h3><p>Ceiling fans are great for circulating both warm air &amp; cool air for year-round comfort, but they can be tricky.</p></div>
  <div class="abs service" style="left:40px;top:685px"><svg class="icon" viewBox="0 0 80 66"><rect x="8" y="14" width="64" height="44" stroke="#fff" stroke-width="3" fill="none"/><rect x="16" y="22" width="40" height="28" stroke="#fff" stroke-width="2" fill="none"/><path d="M28 2l12 12 12-12" stroke="#fff" stroke-width="3" fill="none"/></svg><h3>Cable TV Wiring</h3><p>Ceiling fans are great for circulating both warm air &amp; cool air for year-round comfort, but they can be tricky.</p></div>
  <div class="abs service" style="left:420px;top:685px"><svg class="icon" viewBox="0 0 80 66"><rect x="6" y="12" width="68" height="44" rx="4" stroke="#fff" stroke-width="3" fill="none"/><circle cx="26" cy="34" r="11" stroke="#fff" stroke-width="3" fill="none"/><circle cx="54" cy="34" r="11" stroke="#fff" stroke-width="3" fill="none"/></svg><h3>Electric Meter Install</h3><p>Ceiling fans are great for circulating both warm air &amp; cool air for year-round comfort, but they can be tricky.</p></div>
  <div class="abs service" style="left:800px;top:685px"><svg class="icon" viewBox="0 0 80 66"><path d="M6 56V10M74 56V30M6 40h68M6 30h68" stroke="#fff" stroke-width="3" fill="none"/><rect x="12" y="18" width="20" height="12" rx="4" stroke="#fff" stroke-width="3" fill="none"/></svg><h3>Hospitality</h3><p>Ceiling fans are great for circulating both warm air &amp; cool air for year-round comfort, but they can be tricky.</p></div>
</section>

<div class="abs video" role="img" aria-label="Video still of an electrician in a cap working on an open electrical cabinet">
  <svg class="play" width="80" height="80" viewBox="0 0 80 80"><circle cx="40" cy="40" r="36" stroke="#fff" stroke-width="4" fill="none"/><path d="M32 24l24 16-24 16z" fill="#fff"/></svg>
</div>

<section class="projects">
  <h2 class="abs section-title">We complete projects on time &amp; budget</h2>
  <p class="abs">We’re a friendly team of electricians who understand that you want a reliable &amp; cost efficient solution.</p>
  <div class="abs cta-band">
    <a class="call">Give us a call <svg width="40" height="10" viewBox="0 0 40 10"><path d="M0 5h38M33 1l5 4-5 4" stroke="#fff" stroke-width="2" fill="none"/></svg></a>
    <a class="appoint">Make an appointment today <svg width="40" height="10" viewBox="0 0 40 10"><path d="M0 5h38M33 1l5 4-5 4" stroke="#fff" stroke-width="2" fill="none"/></svg></a>
  </div>
</section>

<section class="reviews">
  <div class="abs base"></div>
  <h2 class="abs section-title">Why clients love us?</h2>
  <div class="abs quote-card">
    <div class="abs mark">“</div>
    <h3 class="abs">Mara J. Ellison</h3>
    <p class="abs">We’re a friendly team of electricians who understand that you want a reliable &amp; cost efficient solution. We’re a friendly team of electricians who understand that you want.</p>
  </div>
  <div class="abs quote-photo" role="img" aria-label="Photo of an electrician kneeling beside a refrigerator repairing its wiring"></div>
  <svg class="tail" width="80" height="46" viewBox="0 0 80 46"><polygon points="0,0 80,0 72,46" fill="#f1f1f1"/></svg>
  <div class="abs brand">K7 Electrical Services Ltd</div>
  <p class="abs tagline">Specializing in the installation, maintenance, service &amp; repair of lighting systems, electrical systems &amp; life safety systems. <strong>Call us today: (014) 555 - 0192</strong></p>
  <div class="abs social"><span></span><span></span><span></span></div>
</section>

<section class="newsletter">
  <h2 class="abs">Subscribe to our Newsletter</h2>
  <p class="abs sub">We’ll keep you with news and updates</p>
  <div class="abs input">Enter you Email</div>
  <a class="abs btn">Subscribe us</a>
  <div class="abs person" role="img" aria-label="Photo of a smiling electrician in blue overalls holding a coil of cable"></div>
</section>

<footer class="site-footer">
  <svg class="foot-shape" width="1200" height="422" viewBox="0 0 1200 422"><polygon points="0,0 330,0 560,422 0,422" fill="#6b2f94"/></svg>
  <div class="abs brand">K7 Electrical<br>Services Ltd</div>
  <h2 class="abs">A Full Service Technology Company.</h2>
  <div class="abs office" style="left:610px;top:108px">
    <h3>Head Office</h3>
    <div class="row"><span class="pin"><svg width="10" height="12" viewBox="0 0 10 12"><path d="M5 12C2 8 0 6 0 4a5 4 0 0110 0c0 2-2 4-5 8z" fill="#fff"/></svg></span><span>418 Larkin Ave<br>Suite 12<br>Eastbrook, NJ 07311</span></div>
    <div class="row"><span class="pin"><svg width="12" height="12" viewBox="0 0 12 12"><path d="M2 1c1 5 4 8 9 9l1-3-3-1-1 1C6 6 5 5 5 4l1-1-1-3z" fill="#fff"/></svg></span><span>Phone: +1 (555) 014 2286</span></div>
  </div>
  <div class="abs office" style="left:900px;top:108px">
    <h3>West Coast Office</h3>
    <div class="row"><span class="pin"><svg width="10" height="12" viewBox="0 0 10 12"><path d="M5 12C2 8 0 6 0 4a5 4 0 0110 0c0 2-2 4-5 8z" fill="#fff"/></svg></span><span>760 Harbor Point<br>Suite 300<br>Bayview, CA 95420</span></div>
  </div>
  <div class="abs office" style="left:610px;top:282px">
    <h3>Technical Center</h3>
    <div class="row"><span class="pin"><svg width="10" height="12" viewBox="0 0 10 12"><path d="M5 12C2 8 0 6 0 4a5 4 0 0110 0c0 2-2 4-5 8z" fill="#fff"/></svg></span><span>2290 Cedar Mill Road<br>Suite 140<br>Oak Ridge, MI 48210</span></div>
  </div>
  <div class="abs office" style="left:900px;top:282px">
    <h3>Head Office</h3>
    <div class="row"><span class="pin"><svg width="10" height="12" viewBox="0 0 10 12"><path d="M5 12C2 8 0 6 0 4a5 4 0 0110 0c0 2-2 4-5 8z" fill="#fff"/></svg></span><span>418 Larkin Ave<br>Suite 12<br>Eastbrook, NJ 07311</span></div>
  </div>
  <div class="abs copyright">© 2018 All rights reserved.</div>
</footer>

</body>
</html>
```